Creative, fresh business card design for Ripplecraft Facades

We need a fresh, creative business card design for Ripplecraft Facades. We are the manufacturer of Ripplecraft Facades in Australia. Wall panels are 2400 x 1200mm panels made from MDF and feature 3D patterns on the face of the panel. The colours to be used are green, silver/grey and white RGB
Red 187
Green 207
Blue 65.

An idea is to possibly use a watermark of one of our designs as a background (like on the "Grids" design on the left hand side of page 2 of our brochure).

Target Market(s)

Interior designers, architects, builders and home renovators

Industry/Entity Type

Business

Contact Information for Business Card

Details to go on the card are:
Our logo (attached),
Slogan: "Decorative panels for interiors and exteriors",
Contact name,
Position,
Mobile phone number,
Business address,
Business phone,
Business fax,
Website and
Email address.

I have attached a few images of our panels and our brochure for reference.

The colours of the business card should feature our logo colours which are: RGB
Red 187
Green 207
Blue 65

Requirements
Must have
• Very modern fonts and design. Some of the designs shown especially the "Prisms" design which is a popular design.
Nice to have
• Creative but simple design. Very contemporary.
Should not have
• Anything ornate or old fashioned.

```html
<!DOCTYPE html>
<html lang="en">
<head>
<meta charset="utf-8">
<title>Ripplecraft Facades – Business Card</title>
<link href="https://fonts.googleapis.com/css2?family=Roboto:wght@300;400;700&display=swap" rel="stylesheet">
<style>
  :root{
    --brand-green:#bbcf41;
    --brand-green-deep:#a9bd32;
    --silver:#9a9b9d;
    --silver-light:#c9cacc;
    --ink:#4a4a4c;
    --paper:#ffffff;
    --paper-shade:#f1f1f1;
    --backdrop:#e6e4df;
  }
  *{box-sizing:border-box;margin:0;padding:0}
  html,body{width:1200px;height:950px;overflow:hidden}
  body{background:var(--backdrop);font-family:'Roboto',Arial,sans-serif;position:relative}

  .card{position:absolute;width:640px;height:366px;overflow:hidden;box-shadow:0 18px 40px rgba(0,0,0,.22)}
  .card-front{left:80px;top:90px;background:var(--paper)}
  .card-back{left:480px;top:494px;background:var(--brand-green)}

  .texture{position:absolute;inset:0}
  .card-front .texture{background:radial-gradient(circle at 50% 45%,var(--paper) 0%,var(--paper-shade) 100%)}
  .card-back .texture{background:radial-gradient(circle at 50% 50%,var(--brand-green) 0%,var(--brand-green-deep) 100%)}

  .edge-bands{position:absolute;left:0;right:0;bottom:0}
  .edge-bands .band-silver{height:10px;background:var(--silver-light)}
  .edge-bands .band-green{height:14px;background:var(--brand-green)}

  .brand{position:absolute;display:flex;align-items:center;gap:12px}
  .brand-mark{width:30px;height:30px;flex:none}
  .brand-name{font-weight:700;letter-spacing:.5px}
  .brand-slogan{position:absolute;font-weight:300;letter-spacing:2px;text-transform:lowercase}

  .card-front .brand{left:40px;top:70px}
  .card-front .brand-mark{background:var(--brand-green)}
  .card-front .brand-name{font-size:25px;color:var(--ink)}
  .card-front .brand-slogan{left:82px;top:110px;font-size:11px;color:var(--silver);line-height:1.5}

  .person{position:absolute;right:40px;top:40px;text-align:right}
  .person-name{font-size:20px;font-weight:700;color:var(--brand-green);letter-spacing:1px;text-transform:uppercase}
  .person-role{font-size:14px;color:var(--silver);margin-top:2px}
  .contacts{list-style:none;margin-top:14px}
  .contacts li{font-size:14px;color:var(--ink);display:flex;justify-content:flex-end;align-items:center;gap:8px;line-height:1.55}
  .contacts svg{width:12px;height:12px;fill:var(--brand-green)}

  .divider{position:absolute;left:40px;right:40px;top:212px;border-top:2px dotted var(--silver)}

  .address{position:absolute;left:40px;top:238px;font-size:14px;color:var(--ink);line-height:1.55}

  .card-back .brand{left:0;right:0;top:140px;justify-content:center}
  .card-back .brand-mark{background:var(--paper)}
  .card-back .brand-name{font-size:32px;color:var(--paper)}
  .card-back .brand-slogan{left:0;right:0;top:192px;text-align:center;font-size:12px;color:var(--paper)}
</style>
</head>
<body>

<section class="card card-front">
  <div class="texture" role="img" aria-label="Embossed concentric ripple pattern on white stock"></div>

  <div class="brand">
    <span class="brand-mark"></span>
    <span class="brand-name">Ripplecraft Facades</span>
  </div>
  <p class="brand-slogan">decorative panels for<br>interiors &amp; landscapes</p>

  <div class="person">
    <p class="person-name">Marcus Hale</p>
    <p class="person-role">CEO&amp;Founder</p>
    <ul class="contacts">
      <li>(555) 214-7730
        <svg viewBox="0 0 24 24" aria-hidden="true"><path d="M6.6 10.8a15.2 15.2 0 0 0 6.6 6.6l2.2-2.2a1 1 0 0 1 1-.25 11.4 11.4 0 0 0 3.6.57 1 1 0 0 1 1 1V20a1 1 0 0 1-1 1A17 17 0 0 1 3 4a1 1 0 0 1 1-1h3.5a1 1 0 0 1 1 1c0 1.25.2 2.45.57 3.57a1 1 0 0 1-.25 1z"/></svg>
      </li>
      <li>(555) 390-1186
        <svg viewBox="0 0 24 24" aria-hidden="true"><rect x="7" y="2" width="10" height="20" rx="2"/></svg>
      </li>
      <li>mhale@ripplecraftfacades.com
        <svg viewBox="0 0 24 24" aria-hidden="true"><path d="M2 5h20v14H2z"/></svg>
      </li>
    </ul>
  </div>

  <div class="divider"></div>

  <address class="address" style="font-style:normal">
    42 Tallow Street<br>
    Brisbane, QLD 4000<br>
    www.ripplecraftfacades.com
  </address>

  <div class="edge-bands">
    <div class="band-silver"></div>
    <div class="band-green"></div>
  </div>
</section>

<section class="card card-back">
  <div class="texture" role="img" aria-label="Embossed concentric ripple pattern on green stock"></div>
  <div class="brand">
    <span class="brand-mark"></span>
    <span class="brand-name">Ripplecraft Facades</span>
  </div>
  <p class="brand-slogan">decorative panels for interiors &amp; landscapes</p>
</section>

</body>
</html>
```